Business Card Design

We need a business card designed for our new company. Prefer a black card with white logo & writing.

Contact Information for Business Card

Ted Galloway, address: 7-4812 Fernhollow Road, Abbotsford, BC, V3K 8R2, Office Phone: 604-712-3390, Cell: 604-947-2164, Email: ted@resinworkshub.ca

Colors

Designer to choose only greyscale colors for use in the design.

```html
<!DOCTYPE html>
<html lang="en">
<head>
<meta charset="utf-8">
<title>Resinworks Hub – Business Card</title>
<link href="https://fonts.googleapis.com/css2?family=Montserrat:wght@400;700;800&display=swap" rel="stylesheet">
<style>
  :root {
    --bg: #1c1c1c;
    --card: #2a2a2a;
    --ink: #ffffff;
    --ink-soft: #d6d6d6;
    --ink-muted: #a8a8a8;
  }
  * { box-sizing: border-box; margin: 0; padding: 0; }
  html, body {
    width: 1200px; height: 1200px; overflow: hidden;
    background: var(--bg);
    font-family: "Montserrat", sans-serif;
    color: var(--ink);
  }
  .canvas {
    width: 1200px; height: 1200px;
    display: flex; flex-direction: column;
    align-items: center; justify-content: center; gap: 60px;
  }
  .card {
    width: 900px; height: 514px;
    background: var(--card);
    position: relative;
    box-shadow: 0 18px 40px rgba(0,0,0,.45);
  }
  .card--front { display: flex; align-items: center; }
  .contact {
    width: 440px; padding-left: 70px;
  }
  .contact__name { font-size: 30px; font-weight: 700; letter-spacing: .5px; }
  .contact__role { font-size: 17px; color: var(--ink-muted); margin-top: 4px; }
  .contact__address {
    font-size: 18px; line-height: 1.35; color: var(--ink-soft);
    margin-top: 34px;
  }
  .contact__list { list-style: none; margin-top: 30px; }
  .contact__item {
    display: flex; align-items: center; gap: 16px;
    font-size: 18px; color: var(--ink-soft);
    margin-bottom: 10px;
  }
  .contact__item svg { width: 18px; height: 18px; flex: none; }
  .brand {
    display: flex; align-items: center; gap: 16px;
    font-weight: 800; color: var(--ink);
    text-transform: uppercase; letter-spacing: 1px;
  }
  .brand__dot { border-radius: 50%; background: var(--ink); flex: none; }
  .card--front .brand { font-size: 40px; margin-left: 20px; }
  .card--front .brand__dot { width: 28px; height: 28px; }
  .card--back { display: flex; align-items: center; justify-content: center; }
  .card--back .brand { font-size: 58px; }
  .card--back .brand__dot { width: 40px; height: 40px; }
</style>
</head>
<body>
<main class="canvas">
  <section class="card card--front">
    <div class="contact">
      <h1 class="contact__name">Ted Galloway</h1>
      <p class="contact__role">owner</p>
      <p class="contact__address">7-4812 Fernhollow Road,<br>Abbotsford, BC, V3K 8R2</p>
      <ul class="contact__list">
        <li class="contact__item">
          <svg viewBox="0 0 24 24" fill="var(--ink)"><path d="M6.6 10.8a15.1 15.1 0 0 0 6.6 6.6l2.2-2.2a1 1 0 0 1 1-.25 11.4 11.4 0 0 0 3.6.57 1 1 0 0 1 1 1V20a1 1 0 0 1-1 1A17 17 0 0 1 3 4a1 1 0 0 1 1-1h3.5a1 1 0 0 1 1 1c0 1.25.2 2.45.57 3.57a1 1 0 0 1-.25 1z"/></svg>
          604-712-3390
        </li>
        <li class="contact__item">
          <svg viewBox="0 0 24 24" fill="none" stroke="var(--ink)" stroke-width="2"><rect x="6" y="2" width="12" height="20" rx="2"/><line x1="11" y1="18" x2="13" y2="18"/></svg>
          604-947-2164
        </li>
        <li class="contact__item">
          <svg viewBox="0 0 24 24" fill="var(--ink)"><path d="M2 5h20v14H2z" opacity="0"/><path d="M2 6l10 7 10-7v12H2z"/><path d="M2 5h20l-10 7z"/></svg>
          ted@resinworkshub.ca
        </li>
        <li class="contact__item">
          <svg viewBox="0 0 24 24" fill="none" stroke="var(--ink)" stroke-width="2"><circle cx="12" cy="12" r="9"/><path d="M3 12h18M12 3c3 3 3 15 0 18M12 3c-3 3-3 15 0 18"/></svg>
          www.resinworkshub.ca
        </li>
      </ul>
    </div>
    <div class="brand"><span class="brand__dot"></span>Resinworks Hub</div>
  </section>

  <section class="card card--back">
    <div class="brand"><span class="brand__dot"></span>Resinworks Hub</div>
  </section>
</main>
</body>
</html>
```